Stationery for Villa Marenta Design Hotel**

Who we are:

Wander on an isolated beach while breathing in the fresh, salty, sea air. Listen to the warm Pacific wind rustling through green palm trees as you walk to a pristine lagoon. Feel the delicious warmth of the sun kiss your skin; the beach is yours. At Villa Marenta you can experience a vacation in undisturbed, natural beauty. We have created a place for you to find new strength, relaxation, and inner harmony. We offer total rest to the experienced traveler from all over the world.

We are a brand new and smartly built design-hotel (under construction) close to a unique beach and a fantastic surf spot in Huatulco, Southwest Mexico.

As you can see in the attachments, we do have an established corporate design, but as for now still need a format for booklets for information around our hotel and things to do in the area, important numbers (we fill in the content for that one).

Our corporate colors:
green #64b445, brown #b07043, blue #0ab7cf, yellow # f9b02a and #fcc01a, navy #444f69
Corporate fonts:
Krub and Miller Banner.
For further information access:
www.villamarenta.example
https://slidevault.example/view/QmPxLwZrTyKsNbVcHdJe/

Social Media: VillaMarenta

Industry/Entity Type

Hotel

Font styles to use
Other font styles liked:
• Krub, Miller Banner

Requirements
Must have
• Stick to Logo Design, defined corporate elements, logo, colors, fonts and general touch and feel
Nice to have
• Who we are:

Our corporate colors:
Corporate fonts:
Krub and Miller Banner.
www.villamarenta.example

Social Media: VillaMarenta

```html
<!DOCTYPE html>
<html lang="en">
<head>
<meta charset="utf-8">
<title>Villa Marenta Design Hotel – Business Cards</title>
<link rel="stylesheet" href="https://fonts.googleapis.com/css2?family=Krub:wght@400;600;700&family=Gelasio:wght@400&display=swap">
<style>
  :root {
    --bg: #2c2e33;
    --card: #ffffff;
    --teal: #0f8f93;
    --teal-bright: #0ab7cf;
    --green: #64b445;
    --green-light: #9ed46a;
    --brown: #b07043;
    --yellow: #f9b02a;
    --gold: #e0b43a;
    --grey-text: #8a8d92;
  }
  * { box-sizing: border-box; margin: 0; padding: 0; }
  html, body { width: 1200px; height: 900px; overflow: hidden; }
  body {
    background: var(--bg);
    display: flex;
    align-items: center;
    justify-content: center;
    gap: 60px;
    font-family: "Krub", sans-serif;
  }
  .card {
    position: relative;
    width: 520px;
    height: 300px;
    border-radius: 22px;
    background: var(--card);
    overflow: hidden;
    box-shadow: 0 14px 30px rgba(0,0,0,.35);
  }
  .card__art { position: absolute; inset: 0; width: 100%; height: 100%; }

  /* back: contact details */
  .card--back { background: linear-gradient(115deg, #ffffff 0%, #f4f4f5 45%, #ffffff 46%, #eeeff0 100%); }
  .contact { position: absolute; left: 58px; top: 44px; }
  .contact__name { font-weight: 700; font-size: 27px; color: var(--teal); line-height: 1.1; }
  .contact__role { font-size: 15px; color: var(--grey-text); margin: 2px 0 12px; }
  .contact__list { list-style: none; }
  .contact__item {
    display: flex; align-items: center; gap: 9px;
    font-family: "Gelasio", serif; font-size: 14px; color: var(--teal);
    line-height: 1; margin-bottom: 9px;
  }
  .contact__icon { width: 14px; height: 14px; flex: none; }
  .brand-mark {
    position: absolute; right: 34px; bottom: 40px;
    display: flex; align-items: center; gap: 8px;
  }
  .brand-mark__square { width: 14px; height: 14px; background: var(--gold); }
  .brand-mark__name { font-weight: 600; font-size: 17px; color: var(--gold); }

  /* front: brand */
  .brand-front {
    position: absolute; left: 50%; top: 50%; transform: translate(-50%, -50%);
    display: flex; align-items: center; gap: 12px;
  }
  .brand-front__square { width: 22px; height: 22px; background: var(--gold); }
  .brand-front__name { font-weight: 600; font-size: 30px; color: var(--gold); letter-spacing: 1px; }
</style>
</head>
<body>

  <section class="card card--back" aria-label="Business card, contact side">
    <svg class="card__art" viewBox="0 0 520 300" aria-hidden="true">
      <line x1="30" y1="0" x2="30" y2="110" stroke="var(--teal-bright)" stroke-width="3"/>
      <line x1="30" y1="190" x2="30" y2="300" stroke="var(--teal-bright)" stroke-width="3"/>
    </svg>
    <div class="contact">
      <h1 class="contact__name">Example Name</h1>
      <p class="contact__role">Designation</p>
      <ul class="contact__list">
        <li class="contact__item">
          <svg class="contact__icon" viewBox="0 0 14 14"><rect width="14" height="14" rx="2" fill="var(--teal)"/><path d="M7 2.5a3 3 0 0 1 3 3c0 2.3-3 6-3 6s-3-3.7-3-6a3 3 0 0 1 3-3z" fill="#fff"/><circle cx="7" cy="5.5" r="1.1" fill="var(--teal)"/></svg>
          Villa Marenta, Playa Serena, Huatulco, Oaxaca, Mexiko
        </li>
        <li class="contact__item">
          <svg class="contact__icon" viewBox="0 0 14 14"><rect width="14" height="14" rx="2" fill="var(--teal)"/><path d="M4 3h2l1 2.5-1.3 1a6 6 0 0 0 2.8 2.8l1-1.3L12 9v2a1 1 0 0 1-1 1A8 8 0 0 1 3 4a1 1 0 0 1 1-1z" fill="#fff"/></svg>
          +52 1 (555) 014 2290
        </li>
        <li class="contact__item">
          <svg class="contact__icon" viewBox="0 0 14 14"><rect width="14" height="14" rx="2" fill="var(--teal)"/><rect x="3" y="4" width="8" height="6" fill="#fff"/><path d="M3 4l4 3.3L11 4" fill="none" stroke="var(--teal)" stroke-width="1"/></svg>
          hello@villamarenta.example
        </li>
        <li class="contact__item">
          <svg class="contact__icon" viewBox="0 0 14 14"><rect width="14" height="14" rx="2" fill="var(--teal)"/><circle cx="7" cy="7" r="4" fill="none" stroke="#fff" stroke-width="1.1"/><path d="M3 7h8M7 3c-2 2.5-2 5.5 0 8M7 3c2 2.5 2 5.5 0 8" fill="none" stroke="#fff" stroke-width="0.9"/></svg>
          www.villamarenta.example
        </li>
      </ul>
    </div>
    <div class="brand-mark">
      <span class="brand-mark__square"></span>
      <span class="brand-mark__name">Villa Marenta</span>
    </div>
  </section>

  <section class="card card--front" aria-label="Business card, brand side">
    <svg class="card__art" viewBox="0 0 520 300" aria-hidden="true">
      <polygon points="0,0 105,0 40,300 0,300" fill="var(--brown)"/>
      <polygon points="0,0 105,0 70,160 0,120" fill="var(--yellow)"/>
      <polygon points="420,0 520,0 520,300 470,300" fill="var(--teal-bright)"/>
      <polygon points="455,130 520,110 520,300 410,300" fill="var(--green-light)"/>
      <polygon points="480,190 520,180 520,300 405,300" fill="var(--green)"/>
    </svg>
    <div class="brand-front">
      <span class="brand-front__square"></span>
      <span class="brand-front__name">Villa Marenta</span>
    </div>
  </section>

</body>
</html>
```